Private practice for psychiatry and psychotherapy needs a business card and logo

I need a logo and business card design for my private practice for psychiatry and psychotherapy. The optional names for my practice are: Vorsteling Praktijk voor Psychiatrie en Psychotherapie, or short: Praktijk Vorsteling.
I am a (child and adolescent) psychiatrist and psychotherapist. I diagnose and treat infants, children, adolescents and adults with psychiatric symptoms/disorders. I also give supervision to colleagues about their own treatments. My work is characterised by personal involvement, transparence, creativity and professionality.
I would like to have an appealing, light and bright, yet basic design that invites people (both children and adults) to contact me, gives trust and hope, without loosing professional appearance.
I uploaded my contact information which should not necessarily be all included (in this form) on the card as long as people know how to contact me. Please feel free to be creative!
Please note that my website is only temporarely and need a new design and update too!

Target Market(s)

Clients and patients (children, adolescents, adults) with psychiatric symptoms who need diagnosis and treatment. I work with private clients and patients through medical insurances.

Industry/Entity Type

Mental Health

Contact Information for Business Card

Dr. Ilse Vorsteling-ter Haaf
Psychiater/Kinder- en Jeugdpsychiater
Jorisvan Heultstraat 14
3071 PW Rotterdam
t: 06-58190274
e: info@praktijkvorsteling.nl
i: www.praktijkvorsteling.nl

Logo Text

Praktijk Vorsteling voor Psychiatrie en Psychotherapie; or short: Praktijk Vorsteling

Font styles to use
Sans Serif
Other font styles liked:
• up to designer

Requirements
Must have
• Appealing, light, bright, creative, trustful, professional and unique.

```html
<!DOCTYPE html>
<html lang="nl">
<head>
<meta charset="utf-8">
<title>Praktijk Vorsteling – visitekaartje</title>
<link rel="stylesheet" href="https://fonts.googleapis.com/css2?family=Oswald:wght@500;600&family=Open+Sans:wght@400;600&display=swap">
<style>
  :root {
    --backdrop: #242424;
    --card: #ffffff;
    --card-shade: #ececec;
    --ink: #4a4a4a;
    --ink-soft: #6b6b6b;
    --rule: #9a9a9a;
    --accent: #f08a1c;
  }
  * { box-sizing: border-box; margin: 0; padding: 0; }
  html, body { width: 1200px; height: 1000px; overflow: hidden; }
  body {
    background: var(--backdrop);
    display: flex;
    flex-direction: column;
    align-items: center;
    justify-content: center;
    gap: 40px;
    font-family: "Open Sans", Arial, sans-serif;
  }
  .card {
    position: relative;
    width: 700px;
    height: 453px;
    border-radius: 20px;
    background: radial-gradient(ellipse at 30% 20%, var(--card) 55%, var(--card-shade) 100%);
    overflow: hidden;
  }
  /* front */
  .holder { position: absolute; left: 46px; top: 52px; }
  .holder-name {
    font-family: "Oswald", "Arial Narrow", sans-serif;
    font-weight: 600;
    font-size: 26px;
    letter-spacing: 0.5px;
    text-transform: uppercase;
    color: var(--ink);
    line-height: 1.15;
  }
  .holder-role {
    margin-top: 4px;
    font-size: 15px;
    font-weight: 600;
    color: var(--accent);
  }
  .divider {
    position: absolute;
    left: 46px; right: 46px; top: 180px;
    height: 2px;
    background: var(--rule);
  }
  .contact-list {
    position: absolute;
    left: 46px; top: 202px;
    list-style: none;
    font-size: 16px;
    color: var(--ink-soft);
    line-height: 30px;
  }
  .contact-list li { display: flex; align-items: center; gap: 12px; }
  .contact-list svg { width: 15px; height: 15px; fill: var(--accent); flex: none; }
  .contact-list .domain { color: var(--accent); }
  .address {
    position: absolute;
    right: 46px; bottom: 56px;
    text-align: right;
    font-size: 16px;
    font-style: normal;
    color: var(--ink-soft);
    line-height: 24px;
  }
  .brand {
    position: absolute;
    display: flex;
    align-items: center;
    gap: 12px;
  }
  .brand-name {
    font-family: "Oswald", "Arial Narrow", sans-serif;
    font-weight: 600;
    text-transform: uppercase;
    color: var(--ink);
    letter-spacing: 0.5px;
    white-space: nowrap;
  }
  .brand-dot { border-radius: 50%; background: var(--accent); flex: none; }
  .card-front .brand { right: 46px; top: 124px; }
  .card-front .brand-name { font-size: 24px; line-height: 1.2; }
  .card-front .brand-dot { width: 15px; height: 15px; }
  /* back */
  .card-back { display: flex; align-items: center; justify-content: center; }
  .card-back .brand { position: static; gap: 18px; }
  .card-back .brand-name { font-size: 52px; }
  .card-back .brand-dot { width: 30px; height: 30px; }
</style>
</head>
<body>

<section class="card card-front" aria-label="Voorzijde visitekaartje">
  <div class="holder">
    <p class="holder-name">Dr. Ilse Vorsteling-ter Haaf</p>
    <p class="holder-role">Psychiater/Kinder- en Jeugdpsychiater</p>
  </div>

  <div class="brand">
    <span class="brand-name">Praktijk Vorsteling</span>
    <span class="brand-dot"></span>
  </div>

  <div class="divider"></div>

  <ul class="contact-list">
    <li>
      <svg viewBox="0 0 16 16" aria-hidden="true"><path d="M3.6 1.2l2.3 2.6-1.2 1.8c.9 2 2.6 3.8 4.7 4.8l1.8-1.2 2.6 2.3-1.3 2.6C7.2 13.5 2.5 8.8 1 3.5z"/></svg>
      <span>06-58190274</span>
    </li>
    <li>
      <svg viewBox="0 0 16 16" aria-hidden="true"><path d="M1 3h14v10H1z M1.5 3.5l6.5 5.5 6.5-5.5" stroke="#fff" stroke-width="1.2"/></svg>
      <span>info@praktijkvorsteling.nl</span>
    </li>
    <li>
      <svg viewBox="0 0 16 16" aria-hidden="true"><circle cx="8" cy="8" r="7"/><path d="M1 8h14M8 1c-3 3.5-3 10.5 0 14M8 1c3 3.5 3 10.5 0 14" stroke="#fff" stroke-width="1.1" fill="none"/></svg>
      <span>www.<span class="domain">praktijkvorsteling</span>.nl</span>
    </li>
  </ul>

  <address class="address">
    Jorisvan Heultstraat 14 3071<br>PW Rotterdam
  </address>
</section>

<section class="card card-back" aria-label="Achterzijde visitekaartje">
  <div class="brand">
    <span class="brand-name">Praktijk Vorsteling</span>
    <span class="brand-dot"></span>
  </div>
</section>

</body>
</html>
```